We are a new company with 2 divisions a medical research and medical product sales. We need a company logo and Business Cards. The design files need to be provided to us in Adobe Photoshop CS 5.1.

Target Market(s)

Medical Community

Industry/Entity Type

Medical

Contact Information for Business Card

Company Name - Harrowgate Lifesciences LLC
Company Address 4127 Larkspur Ave Suite 7, Gainesville Fl 32614

Requirements
Must have
• The design files need to be provided to us in Adobe Photoshop CS 5.1.

```html
<!DOCTYPE html>
<html lang="en">
<head>
<meta charset="utf-8">
<title>Harrowgate Lifesciences LLC – Business Card</title>
<link rel="stylesheet" href="https://fonts.googleapis.com/css2?family=EB+Garamond:wght@400;600;700&display=swap">
<style>
  :root {
    --page-bg: #e9e6e1;
    --card-bg: #ffffff;
    --brand-green: #2f8a1f;
    --band-green: #c3da78;
    --ghost-mark: #eef3eb;
    --ink: #1c1c1c;
    --name-grey: #7a7a7a;
  }
  * { margin: 0; padding: 0; box-sizing: border-box; }
  html, body {
    width: 1200px; height: 900px; overflow: hidden;
    background: var(--page-bg);
    font-family: "EB Garamond", Garamond, serif;
  }
  .card {
    position: absolute; left: 75px; top: 150px;
    width: 1050px; height: 600px;
    background: var(--card-bg);
    box-shadow: 0 6px 24px rgba(0,0,0,.15);
    overflow: hidden;
  }
  .card-art { position: absolute; inset: 0; }
  .brand {
    position: absolute; left: 55px; top: 55px;
    display: flex; align-items: center; gap: 26px;
  }
  .brand-dot {
    width: 150px; height: 150px; border-radius: 50%;
    background: var(--brand-green); flex: none;
  }
  .brand-name {
    color: var(--brand-green);
    font-weight: 400; font-size: 54px; line-height: .95;
    text-transform: uppercase; letter-spacing: .5px;
  }
  .contact {
    position: absolute; left: 70px; top: 372px;
    color: var(--ink); font-size: 29px; line-height: 34px;
    list-style: none;
  }
  .holder {
    position: absolute; right: 45px; top: 400px; text-align: right;
  }
  .holder-name {
    color: var(--name-grey); font-size: 38px; font-weight: 700; line-height: 1;
  }
  .holder-title { color: var(--ink); font-size: 27px; line-height: 1.2; }
</style>
</head>
<body>
  <section class="card" aria-label="Business card">
    <svg class="card-art" width="1050" height="600" viewBox="0 0 1050 600" aria-hidden="true">
      <circle class="ghost-mark" cx="830" cy="300" r="175" fill="var(--ghost-mark)"/>
      <polygon class="contact-band" points="0,335 1050,525 1050,600 0,600" fill="var(--band-green)"/>
    </svg>

    <div class="brand">
      <span class="brand-dot"></span>
      <h1 class="brand-name">Harrowgate<br>Lifesciences LLC.</h1>
    </div>

    <ul class="contact">
      <li>4127 Larkspur Ave Suite 7</li>
      <li>Gainesville Fl 32614</li>
      <li>Phone: 352 555 0148</li>
      <li>Email: contact@harrowgatels.com</li>
      <li>www.harrowgatels.com</li>
    </ul>

    <div class="holder">
      <p class="holder-name">Elias Marrow</p>
      <p class="holder-title">Chief Executive Officer</p>
    </div>
  </section>
</body>
</html>
```